Letter and Envelope Design For Harborline Realty

Please design a letter and an envelope incorporating our logo (See Attached). We are also launched a business card contest. Since we want them to match, please feel free to submit a design for both the business card and also the letter design and envelope.

Requirements
Must have
• The envelope, the letter and the business cards must match somehow connecting the designs. We want them to have something that holds them together besides the logo.

```html
<!DOCTYPE html>
<html lang="en">
<head>
<meta charset="utf-8">
<title>Harborline Realty — Stationery</title>
<link href="https://fonts.googleapis.com/css2?family=Roboto:wght@400;500&family=Mr+Dafoe&display=swap" rel="stylesheet">
<style>
  :root {
    --backdrop: #666666;
    --paper: #f6f6f5;
    --navy: #0a1a8a;
    --ink: #1f1f1f;
    --body-grey: #6b6b6b;
    --faint: #e6e6e5;
    --flap-faint: rgba(255,255,255,0.12);
  }
  * { box-sizing: border-box; margin: 0; padding: 0; }
  html, body { width: 1200px; height: 816px; overflow: hidden; }
  body {
    background: var(--backdrop);
    font-family: "Roboto", Arial, sans-serif;
    position: relative;
  }
  .sheet { position: absolute; background: var(--paper); overflow: hidden; }

  /* Brand lockup */
  .brand { position: absolute; display: flex; flex-direction: column; align-items: center; color: var(--navy); font-weight: 500; }
  .brand__ring { width: 28px; height: 28px; border: 2px solid var(--navy); border-radius: 50%; margin-bottom: 6px; }
  .brand__name { font-size: 11px; letter-spacing: 1.3px; line-height: 1; }
  .brand__sub { font-size: 7.5px; letter-spacing: 3px; line-height: 1; margin-top: 3px; }
  .brand--light { color: #ffffff; }

  .faint-ring { position: absolute; border-radius: 50%; border: 6px solid var(--faint); }

  /* Contact block */
  .contact { position: absolute; color: var(--ink); font-size: 6.8px; line-height: 9.6px; }
  .contact__row { display: flex; align-items: center; gap: 4px; white-space: nowrap; }
  .contact__row svg { width: 6px; height: 6px; fill: var(--navy); flex: none; }
  .contact__gap { width: 4px; }

  /* Envelope front */
  .envelope-front { left: 142px; top: 221px; width: 474px; height: 213px; }
  .envelope-front .faint-ring { left: 270px; top: 7px; width: 200px; height: 200px; }
  .envelope-front .brand { left: 354px; top: 23px; width: 100px; }
  .envelope-front .contact { left: 22px; top: 160px; }

  /* Envelope back */
  .envelope-back { left: 142px; top: 456px; width: 474px; height: 213px; }
  .envelope-back__flap { position: absolute; left: 0; top: 0; }
  .envelope-back .brand { left: 187px; top: 27px; width: 100px; }

  /* Letterhead */
  .letterhead { left: 670px; top: 130px; width: 392px; height: 554px; }
  .letterhead .faint-ring { left: 74px; top: 154px; width: 248px; height: 248px; }
  .letterhead .brand { left: 263px; top: 54px; width: 100px; }
  .letter { position: absolute; left: 24px; top: 0; width: 343px; color: var(--body-grey); font-size: 5.8px; line-height: 8.8px; }
  .letter__date { position: absolute; top: 104px; }
  .letter__recipient { position: absolute; top: 130px; }
  .letter__recipient strong { color: #444; font-weight: 500; }
  .letter__greeting { position: absolute; top: 184px; }
  .letter__para { position: absolute; text-align: justify; width: 343px; }
  .letter__para--1 { top: 203px; }
  .letter__para--2 { top: 256px; }
  .letter__para--3 { top: 308px; }
  .letter__para--4 { top: 344px; }
  .letter__signer { position: absolute; top: 407px; color: #444; font-weight: 500; }
  .letter__signature { position: absolute; top: 416px; left: 0; font-family: "Mr Dafoe", cursive; color: var(--navy); font-size: 17px; line-height: 20px; }
  .letter__role { position: absolute; top: 442px; }
  .letterhead .contact { left: 24px; top: 496px; }
</style>
</head>
<body>

<!-- Envelope front -->
<section class="sheet envelope-front">
  <div class="faint-ring"></div>
  <div class="brand">
    <div class="brand__ring"></div>
    <div class="brand__name">HARBORLINE</div>
    <div class="brand__sub">REALTY</div>
  </div>
  <div class="contact">
    <div class="contact__row"><svg viewBox="0 0 10 10"><path d="M1 2c0-1 1-1.5 2-1.5h4c1 0 2 .5 2 1.5v1H7V2H3v1H1zM2 4h6l1 5H1z"/></svg>555.555.5555</div>
    <div class="contact__row"><svg viewBox="0 0 10 10"><circle cx="5" cy="5" r="4.5"/></svg>johndoe@yourwebsite.com<span class="contact__gap"></span><svg viewBox="0 0 10 10"><rect x="2" y="0" width="6" height="3"/><rect x="0" y="3.5" width="10" height="4"/><rect x="2" y="8" width="6" height="2"/></svg>www.yourwebsite.com</div>
    <div class="contact__row"><svg viewBox="0 0 10 10"><path d="M5 0a3.5 3.5 0 0 1 3.5 3.5C8.5 6 5 10 5 10S1.5 6 1.5 3.5A3.5 3.5 0 0 1 5 0zm0 2a1.5 1.5 0 1 0 0 3 1.5 1.5 0 0 0 0-3z"/></svg>234 Anywhere, Any City, Any Town, US 1234</div>
  </div>
</section>

<!-- Envelope back -->
<section class="sheet envelope-back">
  <svg class="envelope-back__flap" width="474" height="80" viewBox="0 0 474 80">
    <path d="M0 0 H474 L446 58 Q436 76 412 76 H62 Q38 76 28 58 Z" fill="var(--navy)"/>
    <circle cx="237" cy="42" r="28" fill="none" stroke="var(--flap-faint)" stroke-width="2"/>
  </svg>
  <div class="brand brand--light">
    <div class="brand__name">HARBORLINE</div>
    <div class="brand__sub">REALTY</div>
  </div>
</section>

<!-- Letterhead -->
<section class="sheet letterhead">
  <div class="faint-ring"></div>
  <div class="brand">
    <div class="brand__ring"></div>
    <div class="brand__name">HARBORLINE</div>
    <div class="brand__sub">REALTY</div>
  </div>
  <div class="letter">
    <p class="letter__date">30/20/2016</p>
    <p class="letter__recipient"><strong>Mr. XYZ Smith</strong><br>123, Street No. 123,<br>City Name<br>Pincode-123456</p>
    <p class="letter__greeting">Dear Sir,</p>
    <p class="letter__para letter__para--1">Lorem Ipsum is simply dummy text of the printing and typesetting industry. Lorem Ipsum has been the industry's standard dummy text ever since the 1500s, when an unknown printer took a galley of type and scrambled it to make a type specimen book. It has survived not only five centuries, but also the leap into electronic typesetting, remaining essentially unchanged. It was popularised in the 1960s with the release of Letraset sheets containing Lorem Ipsum passages, and more recently with desktop publishing software including versions of Lorem Ipsum.</p>
    <p class="letter__para letter__para--2">Lorem Ipsum is simply dummy text of the printing and typesetting industry. Lorem Ipsum has been the industry's standard dummy text ever since the 1500s, when an unknown printer took a galley of type and scrambled it to make a type specimen book. It has survived not only five centuries, but also the leap into electronic typesetting, remaining essentially unchanged. It was popularised in the 1960s with the release of Letraset sheets containing Lorem Ipsum passages, and more recently with desktop publishing software including versions of Lorem Ipsum.</p>
    <p class="letter__para letter__para--3">Lorem Ipsum is simply dummy text of the printing and typesetting industry. Lorem Ipsum has been the industry's standard dummy text ever since the 1500s, when an unknown printer took a galley of type and scrambled it to make a type specimen book.</p>
    <p class="letter__para letter__para--4">Lorem Ipsum is simply dummy text of the printing and typesetting industry. Lorem Ipsum has been the industry's standard dummy text ever since the 1500s, when an unknown printer took a galley of type and scrambled it to make a type specimen book.</p>
    <p class="letter__signer">Your Name</p>
    <p class="letter__signature">Your Signature</p>
    <p class="letter__role">CEO &nbsp;|&nbsp; Owner</p>
  </div>
  <div class="contact">
    <div class="contact__row"><svg viewBox="0 0 10 10"><path d="M1 2c0-1 1-1.5 2-1.5h4c1 0 2 .5 2 1.5v1H7V2H3v1H1zM2 4h6l1 5H1z"/></svg>555.555.5555</div>
    <div class="contact__row"><svg viewBox="0 0 10 10"><circle cx="5" cy="5" r="4.5"/></svg>johndoe@yourwebsite.com<span class="contact__gap"></span><svg viewBox="0 0 10 10"><rect x="2" y="0" width="6" height="3"/><rect x="0" y="3.5" width="10" height="4"/><rect x="2" y="8" width="6" height="2"/></svg>www.yourwebsite.com</div>
    <div class="contact__row"><svg viewBox="0 0 10 10"><path d="M5 0a3.5 3.5 0 0 1 3.5 3.5C8.5 6 5 10 5 10S1.5 6 1.5 3.5A3.5 3.5 0 0 1 5 0zm0 2a1.5 1.5 0 1 0 0 3 1.5 1.5 0 0 0 0-3z"/></svg>234 Anywhere, Any City, Any Town, US 1234</div>
  </div>
</section>

</body>
</html>
```